VOMRA Pty Ltd Business Card

Looking for a simple yet eye-catching double-sided business card design using my company logo on one side and contact details on the other.

Target Market(s)

Government

Industry/Entity Type

Communication Systems Engineering

Contact Information for Business Card

VOMRA Pty Ltd

Requirements
Nice to have
• Would be great to have a QR code so details can be scanned into contacts

```html
<!DOCTYPE html>
<html lang="en">
<head>
<meta charset="utf-8">
<title>VOMRA Pty Ltd Business Card</title>
<link rel="stylesheet" href="https://fonts.googleapis.com/css2?family=Open+Sans:wght@400;600;700&display=swap">
<style>
  :root {
    --stage: #e6e4e1;
    --card: #1f2024;
    --card-deep: #18191c;
    --brand-grey: #3b4249;
    --slate-bar: #363d44;
    --text-light: #f2f2f2;
    --silver: #b9bcc0;
    --icon: #7d848b;
    --emboss: #2b2d32;
  }
  * { margin: 0; padding: 0; box-sizing: border-box; }
  html, body { width: 1200px; height: 780px; overflow: hidden; }
  body {
    background: var(--stage);
    font-family: "Open Sans", Arial, sans-serif;
    position: relative;
  }
  .card {
    position: absolute;
    top: 235px;
    width: 540px;
    height: 310px;
    background: var(--card);
    box-shadow: 0 10px 24px rgba(0,0,0,0.25);
    overflow: hidden;
  }
  .card--front { left: 40px; }
  .card--back { left: 620px; }

  .brand {
    position: absolute;
    left: 30px;
    top: 26px;
    display: flex;
    align-items: center;
    gap: 14px;
  }
  .brand__mark {
    width: 34px;
    height: 34px;
    background: var(--brand-grey);
  }
  .brand__name {
    font-size: 44px;
    font-weight: 600;
    letter-spacing: 4px;
    color: var(--brand-grey);
    line-height: 1;
  }

  .contact {
    position: absolute;
    left: 30px;
    top: 112px;
    color: var(--text-light);
    font-size: 13.5px;
    line-height: 1.4;
  }
  .contact__address { margin-bottom: 6px; }
  .contact__row {
    display: flex;
    align-items: center;
    gap: 8px;
  }
  .contact__icon { width: 11px; height: 11px; fill: none; stroke: var(--icon); stroke-width: 1.6; }

  .person {
    position: absolute;
    right: 30px;
    top: 118px;
    text-align: right;
    z-index: 1;
  }
  .person__name {
    font-size: 32px;
    line-height: 1.1;
    font-weight: 700;
    color: var(--text-light);
  }
  .person__first { color: var(--brand-grey); font-weight: 600; }
  .person__role {
    font-size: 16px;
    color: var(--text-light);
    margin-top: 2px;
  }
  .accent-bar {
    position: absolute;
    right: 0;
    top: 150px;
    width: 20px;
    height: 44px;
    background: var(--slate-bar);
  }

  .emblem-area {
    position: absolute;
    left: 240px;
    top: 196px;
    width: 230px;
    height: 114px;
    background: radial-gradient(ellipse at 55% 65%, var(--emboss) 0%, var(--card) 72%);
  }

  .back-pattern {
    position: absolute;
    inset: 0;
    background: linear-gradient(135deg, var(--card-deep) 0%, var(--card) 55%, #2d2f34 100%);
  }
  .back-brand {
    position: absolute;
    left: 50%;
    bottom: 34px;
    transform: translateX(-50%);
    display: flex;
    align-items: center;
    gap: 10px;
  }
  .back-brand__mark {
    width: 18px;
    height: 18px;
    background: var(--silver);
  }
  .back-brand__name {
    font-size: 22px;
    font-weight: 600;
    letter-spacing: 3px;
    color: var(--silver);
    line-height: 1;
  }
</style>
</head>
<body>
  <section class="card card--front" aria-label="Business card, contact side">
    <div class="brand">
      <span class="brand__mark"></span>
      <span class="brand__name">VOMRA</span>
    </div>

    <div class="contact">
      <p class="contact__address">14-16 Harwood Lane Marlowe<br>NSW 2031 Australia</p>
      <p class="contact__row">
        <svg class="contact__icon" viewBox="0 0 12 12"><path d="M3 1 L5 3.5 L3.8 5 Q5 7.5 7 8.2 L8.5 7 L11 9 L9.5 11 Q4 10 1 3 Z"/></svg>
        (555) 014-2287
      </p>
      <p class="contact__row">
        <svg class="contact__icon" viewBox="0 0 12 12"><circle cx="6" cy="6" r="5"/><path d="M1 6 H11 M6 1 Q3 6 6 11 M6 1 Q9 6 6 11"/></svg>
        www.vomra.com.au
      </p>
      <p class="contact__row">
        <svg class="contact__icon" viewBox="0 0 12 12"><rect x="1" y="2.5" width="10" height="7"/><path d="M1 2.5 L6 6.5 L11 2.5"/></svg>
        admin@vomra.com.au
      </p>
    </div>

    <div class="emblem-area" role="img" aria-label="Embossed circuit-tree emblem of the brand"></div>

    <div class="accent-bar"></div>
    <div class="person">
      <p class="person__name"><span class="person__first">Jordan</span> Mercer</p>
      <p class="person__role">Co-Founder</p>
    </div>
  </section>

  <section class="card card--back" aria-label="Business card, brand side">
    <div class="back-pattern" role="img" aria-label="Repeating embossed brand emblem pattern on charcoal"></div>
    <div class="back-brand">
      <span class="back-brand__mark"></span>
      <span class="back-brand__name">VOMRA</span>
    </div>
  </section>
</body>
</html>
```